Computer consultant business card

Bexil Software is a newly started computer consulting company. It's a small one-man company that provides mostly Vornix applications but also websites in collaboration with designers. I'm running this company on the side of full time university studies.

I want the final design to be clean and memorable. Be creative! :)

Some inspiration:
http://www.pixelmarta.com/design/48317
http://www.pixelmarta.com/design/2739164/business-card-design-by-frostlynk
http://www.pixelmarta.com/design/604281/business-card-design-by-koralind-vestrabanu

See attachment for my company logo.
Updates

I would like to thank everyone for submitting! I'll need a couple of days to review and ultimately select a design.

Target Market(s)

Non-technical entrepreneurs and small companies.

Industry/Entity Type

University

Requirements
Must have
• My company logo.
In any way, both colors from my logo.
First- and last name, e-mail and phone number.
Double-sided design.
Nice to have
• Something creative with the symbol in my logo

```html
<!DOCTYPE html>
<html lang="en">
<head>
<meta charset="utf-8">
<title>Bexil Software – Business Card</title>
<link rel="stylesheet" href="https://fonts.googleapis.com/css2?family=Quicksand:wght@400;500;600&display=swap">
<style>
  :root {
    --page-bg: #e9ecee;
    --card-white: #ffffff;
    --ink-dark: #3a3a3c;
    --ink-grey: #444446;
    --brand-blue: #2a7fe0;
    --sky-light: #4cc0ec;
    --sky-deep: #1590d0;
    --pattern-dark: #3b4a55;
    --pattern-blue: #3d86e6;
  }
  * { box-sizing: border-box; margin: 0; padding: 0; }
  html, body {
    width: 1200px;
    height: 960px;
    overflow: hidden;
  }
  body {
    background: var(--page-bg);
    font-family: "Quicksand", sans-serif;
    display: flex;
    flex-direction: column;
    align-items: center;
    justify-content: center;
    gap: 44px;
  }
  .card {
    width: 700px;
    height: 400px;
    position: relative;
    box-shadow: 0 6px 18px rgba(0, 0, 0, 0.12);
  }

  /* Front side */
  .card-front {
    background: var(--card-white);
    padding: 0 0 0 92px;
  }
  .brand {
    position: absolute;
    top: 62px;
    left: 160px;
    display: flex;
    align-items: center;
    gap: 26px;
  }
  .brand-dot {
    width: 92px;
    height: 92px;
    border-radius: 50%;
    background: var(--brand-blue);
  }
  .brand-name {
    font-size: 104px;
    font-weight: 500;
    color: var(--ink-dark);
    letter-spacing: 1px;
    line-height: 1;
  }
  .holder-name {
    position: absolute;
    top: 238px;
    left: 92px;
    font-size: 27px;
    font-weight: 500;
    color: var(--ink-grey);
    letter-spacing: 1.5px;
    text-transform: uppercase;
  }
  .contact {
    position: absolute;
    top: 318px;
    left: 92px;
    display: flex;
    gap: 8px;
    font-size: 17px;
    line-height: 22px;
    color: var(--ink-grey);
  }
  .contact-labels {
    color: var(--brand-blue);
    padding-right: 8px;
    border-right: 1.5px solid var(--brand-blue);
    text-align: center;
  }

  /* Back side */
  .card-back {
    background: radial-gradient(ellipse at 50% 45%, var(--sky-light) 0%, var(--sky-deep) 80%);
    display: flex;
    align-items: center;
    justify-content: center;
  }
  .back-pattern {
    width: 620px;
    height: 170px;
    border-radius: 40px;
    background: linear-gradient(90deg, var(--pattern-dark) 0%, var(--pattern-blue) 25%, var(--pattern-dark) 50%, var(--pattern-blue) 75%, var(--pattern-dark) 100%);
    opacity: 0.55;
  }
</style>
</head>
<body>
  <section class="card card-front" aria-label="Card front">
    <div class="brand">
      <span class="brand-dot" aria-hidden="true"></span>
      <span class="brand-name">bexil</span>
    </div>
    <p class="holder-name">Marin Kessel</p>
    <div class="contact">
      <div class="contact-labels">t<br>e</div>
      <div class="contact-values">555.208.4471<br>marin_kessel@postvale.net</div>
    </div>
  </section>

  <section class="card card-back" aria-label="Card back">
    <div class="back-pattern" role="img" aria-label="Repeating pattern of the brand symbol in dark grey and blue"></div>
  </section>
</body>
</html>
```